Business Card Design for Vintage Jazz

I am a vintage jazz band leader in New York City. My groups play the music of the 1920s, 1930s and 1940s. My website is morvalquist.com for more info on what I do.

I am looking for a two sided business card design that has the look and feel of a really nice business card from the 1930s. I need to convey with the design that my work has that vintage kind of class and style, but also conveys that we are fun and entertaining.

Most importantly it should make a bold staement. If Hal Denbrook had a card, what would it have looked like? I want a card that I feel confident will make an impact and will let people know that my work is te the top that NYC has to offer in vintage jazz..

Note that I have only decided to avoid the "committed payment" option as I have not used this service before. Assuming that I get quality work I will select a design from those presented.

Target Market(s)

people who want to hire my band for events, media, and new fans of the band

Industry/Entity Type

Performing Art

Contact Information for Business Card

Definitely a matte finish, possibly a sort of old style of paper with that brown tint? definitely a thick card.

Requirements
Must have
• FRONT
• My name: Tobin Vashley
• What I do: Bandleader, Guitarist, Vocalist, Songwriter
• Contact Details: morvalquist.com tobin@morvalquist.com 646-555-0148
• BACK
• My Social Media Links:
• facebook.morvalquist.com
• twitter, instagram, linkedin: morvalquist
• I'm also including a photo image I would like to use. The photo's background is not needed, and to be honest isn't really desireable. Just looking to use the image of me.
Nice to have
• I'm attaching which could be used as is, omitted from the card, or altered maybe with text going around the outside of the circle or in some other way. It may need some clean up to the edges of the lettering as we only use it for the website thumbnail.
• If there's space I'd like to include the text "join our mailing list for a free song download: freesong.morvalquist.com" If not perhaps just "Download a Free Song at: freesong.morvalquist.com - something to this end.
Should not have
• anything cartoony. Don't think retro 90s's vision of the swing era, think actual swing era!
• anything modern. Got to look old school
• Try to avoid dark backgrounds. Since we often play in bars and clubs where it is dar, a d
• avoid script fonts.

```html
<!DOCTYPE html>
<html lang="en">
<head>
<meta charset="utf-8">
<title>Tobin Vashley — Business Card</title>
<link rel="stylesheet" href="https://fonts.googleapis.com/css2?family=Source+Sans+3:wght@400;600;700&display=swap">
<style>
  :root {
    --backdrop: #e6e3de;
    --card: #f8f7f3;
    --card-grain: rgba(120, 110, 95, 0.06);
    --ink: #121212;
    --card-shadow: rgba(0, 0, 0, 0.16);
  }
  * { margin: 0; padding: 0; box-sizing: border-box; }
  html, body {
    width: 1200px;
    height: 900px;
    overflow: hidden;
    background: var(--backdrop);
    font-family: "Source Sans 3", "Myriad Pro", sans-serif;
    color: var(--ink);
  }
  .canvas { position: relative; width: 1200px; height: 900px; }

  .card {
    position: absolute;
    background-color: var(--card);
    background-image:
      radial-gradient(circle at 30% 40%, var(--card-grain) 0.6px, transparent 1.2px),
      radial-gradient(circle at 70% 80%, var(--card-grain) 0.6px, transparent 1.2px);
    background-size: 4px 4px, 5px 5px;
    box-shadow: 0 3px 12px var(--card-shadow);
  }
  .card--front { left: 238px; top: 62px; width: 554px; height: 341px; }
  .card--back  { left: 457px; top: 518px; width: 560px; height: 344px; }

  .card__name {
    position: absolute;
    left: 62px; top: 123px;
    font-size: 23px;
    font-weight: 600;
    letter-spacing: 0.2px;
  }
  .contact-list {
    position: absolute;
    left: 64px; top: 164px;
    list-style: none;
  }
  .contact-list__item {
    display: flex;
    align-items: center;
    height: 20px;
    font-size: 15.5px;
  }
  .contact-list__icon {
    width: 11px; height: 11px;
    margin-right: 10px;
    flex: none;
  }

  .brand-mark {
    position: absolute;
    display: flex;
    align-items: center;
    font-weight: 700;
    text-transform: uppercase;
    color: var(--ink);
  }
  .brand-mark__dot {
    border-radius: 50%;
    background: var(--ink);
    flex: none;
  }
  .brand-mark__name { display: block; line-height: 1.05; }
  .card--front .brand-mark {
    left: 322px; top: 112px;
    font-size: 30px;
    letter-spacing: 3px;
  }
  .card--front .brand-mark__dot { width: 22px; height: 22px; margin-right: 12px; }
  .card--back .brand-mark {
    left: 0; right: 0; top: 70px;
    justify-content: center;
    font-size: 21px;
    letter-spacing: 2px;
  }
  .card--back .brand-mark__dot { width: 16px; height: 16px; margin-right: 10px; }

  .card__roles {
    position: absolute;
    left: 0; right: 0; top: 295px;
    text-align: center;
    font-size: 16px;
  }

  .social-list {
    position: absolute;
    left: 0; right: 0; top: 193px;
    list-style: none;
    display: flex;
    flex-direction: column;
    align-items: center;
  }
  .social-list__item {
    display: flex;
    align-items: center;
    height: 25px;
    font-size: 16px;
  }
  .social-list__marker {
    width: 11px; height: 11px;
    margin-right: 8px;
    flex: none;
  }
  .social-list__marker--square { background: var(--ink); }
  .social-list__marker--circle { background: var(--ink); border-radius: 50%; }
  .social-list__marker--open-square { border: 2px solid var(--ink); }
  .social-list__marker--open-circle { border: 2px solid var(--ink); border-radius: 50%; }
</style>
</head>
<body>
<main class="canvas">

  <section class="card card--front" aria-label="Card front">
    <h1 class="card__name">Tobin Vashley</h1>
    <ul class="contact-list">
      <li class="contact-list__item">
        <svg class="contact-list__icon" viewBox="0 0 12 12" aria-hidden="true">
          <path d="M2.4 0.6 L4.3 2.9 L3.2 4.3 Q4.3 6.9 7.6 8.8 L9 7.7 L11.4 9.6 L10 11.4 Q5.6 11.2 2.4 7.6 Q0.4 4.6 0.6 2 Z" fill="currentColor"/>
        </svg>
        646-555-0148
      </li>
      <li class="contact-list__item">
        <svg class="contact-list__icon" viewBox="0 0 12 12" aria-hidden="true">
          <rect x="1" y="2.5" width="10" height="7" fill="currentColor"/>
          <path d="M1 2.8 L6 6.6 L11 2.8" fill="none" stroke="#f8f7f3" stroke-width="1"/>
        </svg>
        tobin@morvalquist.com
      </li>
      <li class="contact-list__item">
        <svg class="contact-list__icon" viewBox="0 0 12 12" aria-hidden="true">
          <circle cx="6" cy="6" r="5.2" fill="currentColor"/>
          <path d="M6 0.8 V11.2 M0.8 6 H11.2" stroke="#f8f7f3" stroke-width="0.8"/>
        </svg>
        morvalquist.com
      </li>
    </ul>

    <div class="brand-mark">
      <span class="brand-mark__dot"></span>
      <span><span class="brand-mark__name">Tobin</span><span class="brand-mark__name">Vashley</span></span>
    </div>

    <p class="card__roles">Bandleader, Guitarist, Vocalist, Songwriter</p>
  </section>

  <section class="card card--back" aria-label="Card back">
    <div class="brand-mark">
      <span class="brand-mark__dot"></span>
      <span><span class="brand-mark__name">Tobin</span><span class="brand-mark__name">Vashley</span></span>
    </div>
    <ul class="social-list">
      <li class="social-list__item"><span class="social-list__marker social-list__marker--square"></span>morvalquist.com</li>
      <li class="social-list__item"><span class="social-list__marker social-list__marker--circle"></span>morvalquist</li>
      <li class="social-list__item"><span class="social-list__marker social-list__marker--open-square"></span>morvalquist</li>
      <li class="social-list__item"><span class="social-list__marker social-list__marker--open-circle"></span>morvalquist</li>
    </ul>
  </section>

</main>
</body>
</html>
```